Cafe Menu Required

We need a menu for our coffee shop.
I would like something very much the same as what I have attached.

I have attached a word doc with the items needed on the menu.

I have also attached our logo

I would like to print these on A3 size poster

Cafe

```html
<!DOCTYPE html>
<html lang="en">
<head>
<meta charset="utf-8">
<title>Remedy Canteen Menu</title>
<link href="https://fonts.googleapis.com/css2?family=PT+Serif:wght@400;700&display=swap" rel="stylesheet">
<style>
:root{
  --page:#e9e6e1;
  --board:#141414;
  --board-light:#2a2a2a;
  --red:#e3232a;
  --chalk:#f4f2ee;
  --rule:#cfcfcf;
  --paper:#f3f0e4;
  --photo-dark:#3b2a22;
  --photo-mid:#7a5a44;
}
*{margin:0;padding:0;box-sizing:border-box}
html,body{width:1200px;height:968px;overflow:hidden;background:var(--page)}
body{position:relative;font-family:"PT Serif",Georgia,serif;color:var(--chalk)}
.board{
  position:absolute;left:71px;top:127px;width:1058px;height:748px;
  background:
    radial-gradient(ellipse 420px 70px at 480px 215px,rgba(255,255,255,.07),transparent 70%),
    radial-gradient(ellipse 500px 90px at 420px 330px,rgba(255,255,255,.06),transparent 70%),
    radial-gradient(ellipse 380px 60px at 300px 460px,rgba(255,255,255,.05),transparent 70%),
    var(--board);
  box-shadow:6px 10px 18px rgba(0,0,0,.45);
}
.frame{position:absolute;left:0;top:0;width:1200px;height:968px}
.brand{
  position:absolute;left:520px;top:135px;width:136px;height:136px;
  display:flex;align-items:center;justify-content:center;text-align:center;
  font-weight:700;font-size:20px;line-height:1.05;color:var(--chalk);letter-spacing:.5px;
}
.tagline{position:absolute;left:0;width:1200px;top:292px;text-align:center;font-size:23px;letter-spacing:.3px}
.tagline .dash{color:var(--red)}
.photo-card{
  position:absolute;left:912px;top:162px;width:204px;height:166px;background:var(--paper);
  transform:rotate(8deg);box-shadow:3px 5px 10px rgba(0,0,0,.5);
}
.photo-card .photo{
  position:absolute;left:12px;top:12px;right:12px;bottom:22px;
  background:radial-gradient(ellipse at 55% 55%,var(--photo-mid),var(--photo-dark) 75%);
}
.heading{
  position:absolute;font-size:23px;display:flex;align-items:center;gap:6px;
  padding-bottom:6px;border-bottom:1.5px solid var(--rule);
}
.heading.cold{font-weight:700;font-size:19px}
.cross{width:28px;height:28px;background:var(--chalk);position:relative;display:inline-block}
.cross::before,.cross::after{content:"";position:absolute;background:var(--red)}
.cross::before{left:4px;right:4px;top:12px;height:4px}
.cross::after{top:4px;bottom:4px;left:12px;width:4px}
.list{position:absolute;list-style:none;font-size:23px}
.list li{display:flex;justify-content:space-between}
.hot{left:157px;top:394px;width:378px;line-height:29.4px}
.extras{left:606px;top:447px;width:436px;line-height:29.5px}
.cold-list{left:601px;top:651px;width:443px;line-height:30.2px}
</style>
</head>
<body>
<div class="board"></div>

<svg class="frame" viewBox="0 0 1200 968" aria-hidden="true">
  <g fill="none" stroke="var(--red)" stroke-width="6">
    <polyline points="515,207 97,207 97,845 1102,845 1102,335"/>
    <line x1="660" y1="207" x2="925" y2="207"/>
    <circle cx="588" cy="203" r="66" stroke-width="5"/>
  </g>
</svg>

<div class="brand">Remedy<br>Canteen</div>

<div class="photo-card">
  <div class="photo" role="img" aria-label="Photo of two hands holding cups of latte with foam art on a wooden table"></div>
</div>

<p class="tagline">COFFEE <span class="dash">–</span> CATERING <span class="dash">–</span> FOOD TO GO</p>

<h2 class="heading" style="left:128px;top:353px;width:218px;font-weight:400">HOT BEVERAGES <span class="cross"></span></h2>
<ul class="list hot">
  <li><span>Espresso</span><span>3.5</span></li>
  <li><span>Piccolo</span><span>3.5</span></li>
  <li><span>Short Macchiato</span><span>4.0</span></li>
  <li><span>Long Macchiato</span><span>4.5</span></li>
  <li><span>Latte</span><span>4/4.5/5.5</span></li>
  <li><span>Cappucinno</span><span>4/4.5/5.5</span></li>
  <li><span>Flat White</span><span>4/4.50/5.50</span></li>
  <li><span>Long Black</span><span>4/4.50/5.50</span></li>
  <li><span>Hot Chocolate</span><span>4/4.50/5.50</span></li>
  <li><span>White Hot Chocolate</span><span>4/4.50/5.50</span></li>
  <li><span>Mocha</span><span>4.5/5.0/6.0</span></li>
  <li><span>White Choc Mocha</span><span>4.5/5.0/6.0</span></li>
  <li><span>Chai Latte</span><span>4.5/5.0/6.0</span></li>
  <li><span>Dirty Chai</span><span>5.0/5.5/6.5</span></li>
  <li><span>Selection of Teas</span><span>3.8</span></li>
</ul>

<h2 class="heading" style="left:589px;top:396px;width:124px;font-weight:400">EXTRAS <span class="cross"></span></h2>
<ul class="list extras">
  <li><span>Extra Shot</span><span>0.5</span></li>
  <li><span>Decaf</span><span>0.5</span></li>
  <li><span>Syrups – Caramel/Hazelnut/Vanilla</span><span>0.5</span></li>
  <li><span>Soy</span><span>0.5</span></li>
  <li><span>Lactose free</span><span>0.5</span></li>
</ul>

<h2 class="heading cold" style="left:585px;top:599px;width:221px">COLD BEVERAGES <span class="cross"></span></h2>
<ul class="list cold-list">
  <li><span>Iced Latte</span><span>4.5</span></li>
  <li><span>Iced Long Black</span><span>4.5</span></li>
  <li><span>Iced Coffee w/ice cream</span><span>6.0</span></li>
  <li><span>Iced Chocolate w/ice cream</span><span>6.0</span></li>
  <li><span>Coffee Frappe</span><span>6.0</span></li>
  <li><span>Mango Frappe</span><span>6.0</span></li>
</ul>
</body>
</html>
```